sydney wedding photography business needs a business card design

we need a business card design for a sydney based wedding photography and videography business. our business name is :golden hour studio and film. our target clients are 24-35 yrs female. our style is candid, organic, natural, dynamic. we are a team of young photographers and videographers, and help brides to create memories that they will cherish for the rest of their lives. the logo will be provided. we want an elegant design that reflects our style, and also want to give a great impression to our clients that we are one of the best studios in sydney and our brand means quality and premium service.

Target Market(s)

bride to be, 24-35 years old, living in sydney and surrunding areas

Industry/Entity Type

Wedding Photography

Contact Information for Business Card

address: 57 tarrant street, glenmore nsw 2047
mobile: 0431872259
phone: (02) 9163 2408
info@tidewillowstudio.net.au
www.tidewillowstudio.net.au
facebook:tidewillowweddings
instagram:tidewillowweddings

Font styles to use
Serif
Sans Serif

Requirements
Nice to have
• maybe add my slogan"memories beyond eternity" if the layout looks good
Should not have
• no black color, not good idea for wedding biz card

```html
<!DOCTYPE html>
<html lang="en">
<head>
<meta charset="utf-8">
<title>Golden Hour Studio and Film – Business Card</title>
<link rel="stylesheet" href="https://fonts.googleapis.com/css2?family=Montserrat:wght@400;500&display=swap">
<style>
  :root {
    --canvas: #ebe6de;
    --card-ivory: #f8f5ef;
    --mocha: #5b4638;
    --mocha-deep: #4d3a2e;
    --mocha-soft: #6a5344;
    --gold: #c49a3a;
    --gold-light: #d8b468;
    --ink: #3d3029;
    --photo-sky: linear-gradient(135deg, #6fa6d6 0%, #9cc4df 55%, #5f7f4f 100%);
    --photo-cloud: linear-gradient(160deg, #4f6f95 0%, #8aa7c4 60%, #e6e8ec 100%);
    --photo-night: linear-gradient(150deg, #2c3a2c 0%, #4e5a44 50%, #c88a72 100%);
    --photo-indoor: linear-gradient(135deg, #6a4a32 0%, #a67f5d 50%, #eceae6 100%);
  }
  * { box-sizing: border-box; margin: 0; padding: 0; }
  html, body {
    width: 1200px; height: 892px; overflow: hidden;
    background: var(--canvas);
    font-family: "Montserrat", sans-serif;
  }
  .card {
    position: absolute; left: 300px;
    width: 600px; height: 343px;
    overflow: hidden;
    box-shadow: 0 8px 24px rgba(60,45,35,.18);
  }
  /* Front */
  .card-front { top: 50px; background: var(--card-ivory); }
  .front-head {
    position: absolute; left: 0; top: 0; width: 100%; height: 132px;
    display: flex; align-items: center; justify-content: space-between;
    padding: 0 34px;
  }
  .brand-name {
    color: var(--gold); font-weight: 500;
    font-size: 20px; line-height: 1.25; letter-spacing: .4px;
    white-space: nowrap;
  }
  .contact-list { list-style: none; color: var(--ink); font-size: 14px; line-height: 1.45; }
  .contact-list li { display: flex; align-items: center; gap: 8px; white-space: nowrap; }
  .contact-icon {
    width: 14px; height: 14px; background: var(--gold);
    display: inline-flex; align-items: center; justify-content: center; flex: none;
  }
  .rule { position: absolute; left: 0; width: 100%; background: var(--mocha); }
  .rule-top { top: 134px; height: 4px; }
  .photo-strip {
    position: absolute; left: 0; top: 142px; width: 100%; height: 120px;
    display: flex; gap: 4px; background: var(--mocha);
  }
  .photo { flex: 1; }
  .photo-sky { background: var(--photo-sky); }
  .photo-cloud { background: var(--photo-cloud); }
  .photo-night { background: var(--photo-night); }
  .photo-indoor { background: var(--photo-indoor); }
  .address-band {
    position: absolute; left: 0; top: 262px; width: 100%; height: 81px;
    background: var(--mocha);
    display: flex; align-items: center; justify-content: center;
    color: var(--gold-light); font-size: 20px; letter-spacing: .3px;
  }
  /* Back */
  .card-back { top: 470px; background: var(--mocha); }
  .back-brand {
    position: absolute; left: 0; top: 110px; width: 100%;
    text-align: center; color: var(--gold-light);
    font-weight: 500; font-size: 32px; letter-spacing: 1px;
    white-space: nowrap;
  }
  .back-footer {
    position: absolute; left: 0; bottom: 0; width: 100%; height: 70px;
    background: var(--mocha-deep);
    display: flex; align-items: center; justify-content: center; gap: 18px;
    color: var(--gold-light); font-size: 16px; white-space: nowrap;
  }
  .divider { width: 1px; height: 30px; background: var(--gold); }
</style>
</head>
<body>
  <section class="card card-front" aria-label="Business card front">
    <header class="front-head">
      <div class="brand-name">Golden Hour Studio and Film</div>
      <ul class="contact-list">
        <li><span class="contact-icon">
          <svg width="8" height="11" viewBox="0 0 8 11"><rect x="0.5" y="0.5" width="7" height="10" rx="1" fill="none" stroke="#fff"/><circle cx="4" cy="8.6" r=".8" fill="#fff"/></svg>
        </span>0431872259</li>
        <li><span class="contact-icon">
          <svg width="10" height="10" viewBox="0 0 10 10"><path d="M2 1 L4 3 L3 4.2 C3.8 5.6 4.6 6.4 5.8 7 L7 6 L9 8 L7.8 9.3 C4.5 9 1 5.5 0.7 2.2 Z" fill="#fff"/></svg>
        </span>(02) 9163 2408</li>
        <li><span class="contact-icon"></span>tidewillowweddings</li>
        <li><span class="contact-icon"></span>tidewillowweddings</li>
      </ul>
    </header>
    <div class="rule rule-top"></div>
    <div class="photo-strip">
      <div class="photo photo-sky" role="img" aria-label="Wedding couple photo outdoors by a garden gate under blue sky"></div>
      <div class="photo photo-cloud" role="img" aria-label="Bride and groom photo on a terrace under a cloudy sky"></div>
      <div class="photo photo-night" role="img" aria-label="Evening wedding party photo under garden lights"></div>
      <div class="photo photo-indoor" role="img" aria-label="Couple cutting the wedding cake indoors"></div>
    </div>
    <div class="address-band">57 tarrant street, glenmore nsw 2047</div>
  </section>

  <section class="card card-back" aria-label="Business card back">
    <div class="back-brand">Golden Hour Studio and Film</div>
    <footer class="back-footer">
      <span>www.tidewillowstudio.net.au</span>
      <span class="divider"></span>
      <span>info@tidewillowstudio.net.au</span>
    </footer>
  </section>
</body>
</html>
```